Business Card Design & Gift cards, Gift Cert, Donation Card

Retail Gift Store-in addition to Business Cards we'd like sequenced 2 sided Gift cards, Gift Certificate Cards, and Donation Cards.please see examples and email for clarificationlogos attached with examples-
Gift Card, Gift Certificate and Donation Card will all be same style just differant upper right title, with back side info as example.
business card, as example is single sided.
looking for additional ideas for layout

Industry/Entity Type

Business

Contact Information for Business Card

211 Newman St.East Tawas, MI 48730989.362.8730Office@BrewKrew.com

Requirements
Must have
• Blue as per example
• Logos provided
• like gradiant background

```html
<!DOCTYPE html>
<html lang="en">
<head>
<meta charset="utf-8">
<title>Tillow Marsh – Business Card &amp; Gift Card</title>
<link rel="stylesheet" href="https://fonts.googleapis.com/css2?family=Comic+Neue:wght@400;700&display=swap">
<style>
  :root {
    --stage: #3c3c3c;
    --card: #ffffff;
    --ink: #111111;
    --text-grey: #4a4a4a;
    --rule: #6a6a6a;
    --brand-blue: #1a2fc9;
    --band-black: #151515;
    --band-grey: #8a8a8a;
  }
  * { margin: 0; padding: 0; box-sizing: border-box; }
  html, body { width: 1105px; height: 1200px; overflow: hidden; }
  body {
    background: var(--stage);
    font-family: "Comic Neue", "Comic Sans MS", cursive;
    position: relative;
  }
  .card {
    position: absolute;
    left: 196px;
    width: 719px;
    height: 412px;
    background: var(--card);
    border-radius: 26px;
    overflow: hidden;
  }
  .card--business { top: 146px; }
  .card--gift { top: 602px; }

  /* Business card front */
  .brand-name {
    position: absolute;
    left: 36px; top: 168px;
    font-size: 50px;
    font-weight: 400;
    color: var(--ink);
    letter-spacing: 1px;
    line-height: 1;
  }
  .brand-mark {
    position: absolute;
    left: 530px; top: 30px;
    width: 130px; height: 130px;
    border-radius: 50%;
    background: var(--brand-blue);
  }
  .divider {
    position: absolute;
    left: 36px; right: 40px; top: 249px;
    border-top: 2px solid var(--rule);
  }
  .contact, .offerings {
    position: absolute;
    top: 258px;
    font-size: 22px;
    line-height: 27px;
    color: var(--text-grey);
  }
  .contact { left: 36px; }
  .offerings { right: 40px; text-align: right; }
  .contact li, .offerings li { list-style: none; }
  .contact .icon {
    display: inline-block;
    width: 16px; height: 16px;
    margin-right: 8px;
    vertical-align: -1px;
  }
  .card-band {
    position: absolute;
    left: 0; bottom: 0;
    width: 100%; height: 23px;
  }

  /* Gift card back */
  .card-number {
    position: absolute;
    right: 36px; top: 32px;
    font-size: 18px;
    color: var(--ink);
  }
  .field {
    position: absolute;
    left: 56px;
    display: flex;
    align-items: baseline;
    color: var(--ink);
  }
  .field__label { white-space: nowrap; }
  .field__line {
    border-bottom: 1.5px solid var(--rule);
    margin-left: 10px;
    height: 1px;
  }
  .field--large { font-size: 27px; }
  .field--small { font-size: 22px; }
  .field--to { top: 80px; }
  .field--to .field__line { width: 542px; }
  .field--from { top: 138px; }
  .field--from .field__line { width: 515px; }
  .field--issued { top: 222px; }
  .field--issued .field__line { width: 307px; }
  .field--expires { top: 270px; }
  .field--expires .field__line { width: 276px; }
  .field--employee { top: 318px; }
  .field--employee .field__line { width: 327px; margin-left: 26px; }
  .gift-brand {
    position: absolute;
    left: 520px; top: 262px;
    width: 160px;
    text-align: center;
    font-size: 26px;
    font-weight: 700;
    line-height: 1.1;
    color: var(--brand-blue);
  }
</style>
</head>
<body>

<section class="card card--business" aria-label="Business card front">
  <div class="brand-mark" aria-hidden="true"></div>
  <h1 class="brand-name">TILLOW MARSH</h1>
  <div class="divider"></div>
  <ul class="contact">
    <li>482 Larkfield Ave.</li>
    <li>Harbor Bend, MI 48731</li>
    <li><svg class="icon" viewBox="0 0 16 16" aria-hidden="true"><path fill="#111" d="M3.5 1.2l2.4 2.6-1.3 1.8c.9 2 2.7 3.8 4.8 4.8l1.8-1.3 2.6 2.4-1.4 2.6C6.8 13.6 2.4 9.2 1 3z"/></svg>989.517.4296</li>
    <li><svg class="icon" viewBox="0 0 16 16" aria-hidden="true"><rect x="1" y="3" width="14" height="10" fill="#111"/><path d="M1.5 3.5L8 9l6.5-5.5" stroke="#fff" stroke-width="1.4" fill="none"/></svg>Office@TillowMarsh.com</li>
  </ul>
  <ul class="offerings">
    <li>Gourmet Food</li>
    <li>Fine Wines | Gift Baskets</li>
    <li>Kitchen &amp; Bath Accessories</li>
    <li>Candles | Cards | Soaps</li>
  </ul>
  <svg class="card-band" viewBox="0 0 719 23" preserveAspectRatio="none" aria-hidden="true">
    <polygon points="0,0 466,0 461,23 0,23" fill="var(--band-black)"/>
    <polygon points="474,0 719,0 719,23 469,23" fill="var(--band-grey)"/>
  </svg>
</section>

<section class="card card--gift" aria-label="Gift card back">
  <p class="card-number">Card Number : 58724</p>
  <div class="field field--large field--to"><span class="field__label">To :</span><span class="field__line"></span></div>
  <div class="field field--large field--from"><span class="field__label">Form :</span><span class="field__line"></span></div>
  <div class="field field--small field--issued"><span class="field__label">Date&nbsp; Issued :</span><span class="field__line"></span></div>
  <div class="field field--small field--expires"><span class="field__label">Expiration Date :</span><span class="field__line"></span></div>
  <div class="field field--small field--employee"><span class="field__label">Employee :</span><span class="field__line"></span></div>
  <p class="gift-brand">Tillow Marsh</p>
</section>

</body>
</html>
```